Commercial Post Cards

We are looking for 3 postcards that are similar but target 3 commercial property types. they will be 6x9 cards can be front and back or not.
1. Hotel Postcard – Taviqon / Bed Bug Protection
Use the attached Taviqon sample as the primary direction.
The focus should be:
Proactive bed bug prevention and control
Protecting guests and the hotel's reputation
Regular inspections
Documentation and risk management
Professional commercial pest management
The backside should transition into our General Pest Control services, showing that we can be the hotel's complete pest management provider beyond just bed bugs.
2. Apartment Complex Postcard
Target apartment owners, property managers, and management companies.
Focus on:
General pest control
Bed bug control
Rodent control
Preventative pest management
Protecting residents and the property
Reliable, ongoing service and documentation
The message should position us as a full-service pest management partner for multifamily properties.

3. Commercial Building Postcard
Target office buildings, banks, storage facilities, and other commercial properties.

Focus on:
General commercial pest control
Rodent control
Fly management
Recurring service programs
Protecting the property, employees, customers, and reputation

Overall Direction
All three postcards should have a consistent brand and visual style, but each should feel specifically designed for its target market.

We want the messaging to communicate:
Professional • Reliable • Proactive • Locally Owned & Operated • Serving Since 2017

The goal is not to overwhelm the reader with information. These should be marketing pieces that quickly communicate the problem we solve, our expertise, and why a commercial property should contact us.

I have included some of our marketing materials for help with what we do.

```html
<!DOCTYPE html>
<html lang="en">
<head>
<meta charset="utf-8">
<title>Taviqon Hotel Postcard</title>
<link rel="stylesheet" href="https://fonts.googleapis.com/css2?family=Bebas+Neue&family=Arimo:wght@400;700&display=swap">
<style>
:root{
  --backdrop:#e8e9e8;
  --card:#ffffff;
  --orange:#d06232;
  --ink:#2d2d2d;
  --charcoal:#222223;
  --white:#ffffff;
}
*{box-sizing:border-box;margin:0;padding:0}
html,body{width:1200px;height:964px;overflow:hidden;background:var(--backdrop)}
body{position:relative;font-family:"Arimo",Arial,sans-serif;color:var(--ink)}
.postcard{position:absolute;left:115px;top:159px;width:969px;height:646px;background:var(--card);overflow:hidden}
.abs{position:absolute}

.hero-photo{left:336px;top:0;width:633px;height:288px;
  background:linear-gradient(90deg,#ffffff 0%,rgba(255,255,255,0) 22%),
  linear-gradient(160deg,#8a7560 0%,#c9bba8 35%,#ece6dc 55%,#b7a793 80%,#6d5b4a 100%)}

.brand{left:32px;top:52px;font-weight:700;font-size:34px;color:var(--ink);letter-spacing:-0.5px;display:flex;align-items:center;gap:10px}
.brand-dot{width:22px;height:22px;border-radius:50%;background:var(--orange)}

.product-name{left:30px;top:124px;font-family:"Bebas Neue",Impact,sans-serif;font-size:118px;line-height:1;color:var(--charcoal);letter-spacing:-1px;font-weight:400}
.product-name .accent{color:var(--orange)}
.tagline{left:32px;top:226px;font-weight:700;font-size:22px;line-height:27px;color:var(--ink)}

.promise-band{left:0;top:288px;width:969px;height:47px;background:var(--orange);border-bottom:6px solid var(--charcoal)}
.promise-text{left:105px;top:299px;font-weight:700;font-size:14.6px;color:var(--white)}
.band-shield{left:32px;top:278px;width:53px;height:62px}

.headline{left:31px;top:355px;font-family:"Bebas Neue",Impact,sans-serif;font-size:90px;line-height:75px;color:var(--charcoal);font-weight:400;white-space:nowrap}
.headline .accent{color:var(--orange)}

.benefit{display:flex;gap:14px;align-items:flex-start;font-weight:700;font-size:16px;line-height:20px;color:var(--ink)}
.benefit svg{width:33px;height:38px;flex:none;margin-top:-10px}
.benefit span{width:190px}
.benefit.col-2 span{width:175px}

.cta-shield{left:140px;top:520px;width:62px;height:72px;z-index:2}
.cta-bar{left:185px;top:539px;width:614px;height:41px;border:3px solid var(--orange);border-radius:0 12px 12px 0;background:var(--white);display:flex;align-items:center;z-index:1}
.cta-main{height:100%;background:var(--orange);color:var(--white);font-weight:700;font-size:19px;display:flex;align-items:center;padding-left:38px;width:365px;clip-path:polygon(0 0,94% 0,100% 50%,94% 100%,0 100%)}
.cta-rest{font-weight:700;font-size:19px;color:var(--charcoal);padding-left:12px}

.contact-bar{left:0;top:565px;width:969px;height:81px;background:var(--charcoal)}
.contact{display:flex;align-items:center;gap:12px;color:var(--white);font-weight:700;font-size:16px;white-space:nowrap}
.phone-icon{width:25px;height:25px;border-radius:50%;background:var(--orange);display:flex;align-items:center;justify-content:center;flex:none}
.phone-icon svg{width:14px;height:14px}
.contact-main{font-size:25px;line-height:1}
.contact-main small{display:block;text-align:right;font-size:13px;margin-top:2px}
</style>
</head>
<body>
<div class="postcard">
  <div class="abs hero-photo" role="img" aria-label="Photo of a bright, upscale hotel room with a made king bed, lamps, armchairs and window curtains"></div>

  <div class="abs brand"><span class="brand-dot"></span>Brevant Pest Control</div>

  <h1 class="abs product-name">TAVI<span class="accent">QON</span></h1>
  <p class="abs tagline">Quarterly Inspected &amp; Documented<br>Bed Bug Prevention for Hotels</p>

  <div class="abs promise-band"></div>
  <svg class="abs band-shield" viewBox="0 0 53 62" aria-hidden="true">
    <path d="M26.5 2 L50 11 V30 C50 45 39 55 26.5 60 C14 55 3 45 3 30 V11 Z" fill="#fff" stroke="#d06232" stroke-width="4"/>
    <path d="M26.5 9 L44 15.5 V30 C44 41 36 49 26.5 53 C17 49 9 41 9 30 V15.5 Z" fill="#f4f4f4" stroke="#222" stroke-width="1.5"/>
  </svg>
  <p class="abs promise-text">Proactive protection. Quarterly inspected. Documented results. Peace of mind for your guests and your business.</p>

  <h2 class="abs headline">DON’T LET BED<br>BUGS <span class="accent">CHECK IN.</span></h2>

  <div class="abs benefit" style="left:468px;top:364px"><svg viewBox="0 0 34 40"><use href="#tick-shield"/></svg><span>Proactive bed bug prevention and control</span></div>
  <div class="abs benefit" style="left:468px;top:437px"><svg viewBox="0 0 34 40"><use href="#tick-shield"/></svg><span>Protecting guests and the hotel's reputation</span></div>
  <div class="abs benefit" style="left:468px;top:489px"><svg viewBox="0 0 34 40"><use href="#tick-shield"/></svg><span>Regular inspections</span></div>
  <div class="abs benefit col-2" style="left:717px;top:364px"><svg viewBox="0 0 34 40"><use href="#tick-shield"/></svg><span>Documentation and risk management</span></div>
  <div class="abs benefit col-2" style="left:717px;top:416px"><svg viewBox="0 0 34 40"><use href="#tick-shield"/></svg><span>Professional commercial pest management</span></div>

  <div class="abs contact-bar"></div>

  <svg class="abs cta-shield" viewBox="0 0 62 72" aria-hidden="true">
    <path d="M31 2 L59 12 V36 C59 53 46 64 31 70 C16 64 3 53 3 36 V12 Z" fill="#d06232"/>
    <path d="M31 9 L53 17 V36 C53 49 43 58 31 63 C19 58 9 49 9 36 V17 Z" fill="#222223" stroke="#fff" stroke-width="2.5"/>
    <path d="M19 37 L28 46 L44 28" fill="none" stroke="#fff" stroke-width="5" stroke-linecap="round" stroke-linejoin="round"/>
  </svg>
  <div class="abs cta-bar">
    <div class="cta-main">ASK US FOR A CUSTOM QUOTE</div>
    <div class="cta-rest">FOR YOUR PROPERTY.</div>
  </div>

  <div class="abs contact" style="left:32px;top:594px">
    <span class="phone-icon"><svg viewBox="0 0 24 24"><use href="#phone"/></svg></span>
    <span class="contact-main">208-555-0142<small>(Idaho)</small></span>
  </div>
  <div class="abs contact" style="left:272px;top:599px">
    <span class="phone-icon"><svg viewBox="0 0 24 24"><use href="#phone"/></svg></span>Cell: 208-555-0187
  </div>
  <div class="abs contact" style="left:486px;top:599px">
    <span class="phone-icon"><svg viewBox="0 0 24 24"><use href="#phone"/></svg></span>Colorado: 970-555-0163
  </div>
  <div class="abs contact" style="left:737px;top:599px">
    <span class="phone-icon"><svg viewBox="0 0 24 24"><use href="#phone"/></svg></span>www.brevantpest.com
  </div>
</div>

<svg width="0" height="0" style="position:absolute" aria-hidden="true">
  <defs>
    <g id="tick-shield">
      <path d="M17 1 L32 6.5 V20 C32 30 25 36 17 39 C9 36 2 30 2 20 V6.5 Z" fill="#d06232"/>
      <path d="M17 5 L28.5 9 V20 C28.5 27.5 23 32.5 17 35 C11 32.5 5.5 27.5 5.5 20 V9 Z" fill="#222223"/>
      <path d="M11 20 L15.5 24.5 L23.5 15.5" fill="none" stroke="#fff" stroke-width="2.8" stroke-linecap="round" stroke-linejoin="round"/>
    </g>
    <path id="phone" fill="#fff" d="M6.6 10.8c1.4 2.8 3.8 5.1 6.6 6.6l2.2-2.2c.3-.3.7-.4 1-.2 1.1.4 2.300.6 3.6.6.6 0 1 .4 1 1V20c0 .6-.4 1-1 1C10.6 21 3 13.4 3 4c0-.6.4-1 1-1h3.5c.6 0 1 .4 1 1 0 1.3.2 2.5.6 3.6.1.3 0 .7-.2 1z"/>
  </defs>
</svg>
</body>
</html>
```